Web Developer Needs a Business Card Design

I need a personal business card design that represents me as a web developer for potential employers. I would like the background to be a dark color on the front for contrast with my logo and name. The back will have all my information along with a smaller version of the logo. I want something with a modern look and feel, not too conservative. This will be used for potential employers and freelance work.

Industry/Entity Type

Business

Contact Information for Business Card

Front should have my logo and name. The back should have all my personal information which would include: name: Tom Varulek, phone: 570-614-3098, email: tomvarulek@quillbox.net, website url: www.tomvarulek.net, logo, web developer.

Font styles to use
Sans Serif

Requirements
Must have
• Must include my logo. The color palette base color will be the logo color.

```html
<!DOCTYPE html>
<html lang="en">
<head>
<meta charset="utf-8">
<title>Tom Varulek – Business Card</title>
<link href="https://fonts.googleapis.com/css2?family=Open+Sans:wght@400;600&display=swap" rel="stylesheet">
<style>
  :root {
    --card-dark: #1e1613;
    --brand-teal: #4fdcbf;
    --swoosh-light: #86d9c6;
    --swoosh-deep: #5fc2ad;
    --text-light: #f2efec;
    --backdrop: #d9d4ce;
  }
  * { box-sizing: border-box; margin: 0; padding: 0; }
  html, body {
    width: 1200px; height: 892px; overflow: hidden;
    background: var(--backdrop);
    font-family: "Open Sans", sans-serif;
  }
  .canvas {
    position: relative; width: 1200px; height: 892px;
    display: flex; align-items: center; justify-content: center; gap: 80px;
  }
  .card {
    position: relative; background: var(--card-dark); overflow: hidden;
    box-shadow: 0 10px 30px rgba(0,0,0,0.25);
  }
  /* Front: landscape */
  .card--front {
    width: 600px; height: 343px;
    display: flex; flex-direction: column; align-items: center; justify-content: center;
  }
  .brand-ring {
    width: 150px; height: 150px; border-radius: 50%;
    border: 9px solid var(--brand-teal);
    display: flex; align-items: center; justify-content: center;
  }
  .brand-ring__name {
    color: var(--brand-teal); font-weight: 600; font-size: 19px; text-align: center; line-height: 1.15;
  }
  .front-name {
    margin-top: 26px; color: var(--brand-teal); font-weight: 600; font-size: 40px; letter-spacing: 0.5px;
  }
  /* Back: portrait */
  .card--back { width: 343px; height: 600px; }
  .back-mark {
    position: absolute; top: 40px; left: 70px;
    width: 92px; height: 92px; border-radius: 50%;
    border: 6px solid var(--brand-teal);
  }
  .back-info { position: absolute; top: 156px; left: 32px; }
  .back-name { color: var(--brand-teal); font-weight: 600; font-size: 27px; line-height: 1.1; }
  .back-role { color: var(--text-light); font-size: 16px; margin-top: 2px; }
  .contact-list { list-style: none; margin-top: 22px; }
  .contact-item {
    display: flex; align-items: center; gap: 12px;
    color: var(--text-light); font-size: 15px; margin-bottom: 9px;
  }
  .contact-icon {
    width: 16px; height: 16px; background: #5a5350; border-radius: 2px; flex: none;
  }
  .swoosh { position: absolute; left: 0; bottom: 0; width: 343px; height: 600px; }
</style>
</head>
<body>
<main class="canvas">
  <section class="card card--front" aria-label="Card front">
    <div class="brand-ring"><span class="brand-ring__name">Tom<br>Varulek</span></div>
    <h1 class="front-name">Tom Varulek</h1>
  </section>

  <section class="card card--back" aria-label="Card back">
    <svg class="swoosh" viewBox="0 0 343 600" aria-hidden="true">
      <defs>
        <linearGradient id="swooshFill" x1="0" y1="0" x2="1" y2="1">
          <stop offset="0" stop-color="var(--swoosh-light)"/>
          <stop offset="1" stop-color="var(--swoosh-deep)"/>
        </linearGradient>
      </defs>
      <path d="M0 420 C 120 470, 260 420, 343 330 L 343 600 L 300 600 C 230 470, 110 440, 0 455 Z" fill="url(#swooshFill)"/>
    </svg>
    <div class="back-mark" aria-hidden="true"></div>
    <div class="back-info">
      <h2 class="back-name">Tom Varulek</h2>
      <p class="back-role">web developer</p>
      <ul class="contact-list">
        <li class="contact-item">
          <svg class="contact-icon" viewBox="0 0 16 16" aria-hidden="true"><rect width="16" height="16" rx="2" fill="#5a5350"/><path d="M5 3.5l2 2-1 1.2c.6 1.3 1.6 2.3 2.9 2.9l1.1-1 2 2-1.2 1.4C7.6 11.6 4.4 8.4 3.9 4.7z" fill="#f2efec"/></svg>
          570-614-3098</li>
        <li class="contact-item">
          <svg class="contact-icon" viewBox="0 0 16 16" aria-hidden="true"><rect width="16" height="16" rx="2" fill="#5a5350"/><circle cx="8" cy="8" r="4.5" fill="none" stroke="#f2efec" stroke-width="1.2"/><path d="M3.5 8h9M8 3.5c-2 2.5-2 6.5 0 9M8 3.5c2 2.5 2 6.5 0 9" fill="none" stroke="#f2efec" stroke-width="1"/></svg>
          www.tomvarulek.net</li>
        <li class="contact-item">
          <svg class="contact-icon" viewBox="0 0 16 16" aria-hidden="true"><rect width="16" height="16" rx="2" fill="#5a5350"/><rect x="3" y="4.5" width="10" height="7" fill="none" stroke="#f2efec" stroke-width="1.2"/><path d="M3 4.5l5 4 5-4" fill="none" stroke="#f2efec" stroke-width="1.2"/></svg>
          tomvarulek@quillbox.net</li>
      </ul>
    </div>
  </section>
</main>
</body>
</html>
```